I am hosting a banquet called, Copper & Pearl Gala and I need a design to help sell it on Linkora.

Hi all.
No disco balls, please.
I would like a miser-traditional design, classy.

```html
<!DOCTYPE html>
<html lang="en">
<head>
<meta charset="utf-8">
<title>Copper &amp; Pearl Gala – Invitation</title>
<link rel="stylesheet" href="https://fonts.googleapis.com/css2?family=Oranienbaum&family=Cinzel:wght@400&family=Poppins:wght@400;600;700&display=swap">
<style>
  :root {
    --backdrop: #c8c8c8;
    --ink: #0b0b0c;
    --pearl: #f4efe4;
    --pearl-soft: #e8e1d3;
    --copper: #b87333;
    --copper-light: #e0a26a;
    --copper-dark: #7a4520;
    --band-edge: #141110;
    --band-mid: #5a3c27;
    --band-center: #9c7458;
  }
  * { margin: 0; padding: 0; box-sizing: border-box; }
  html, body { width: 1200px; height: 1158px; overflow: hidden; background: var(--backdrop); }
  .invitation {
    position: absolute; left: 115px; top: 99px; width: 925px; height: 925px;
    background: var(--ink); overflow: hidden; color: var(--pearl);
    font-family: "Poppins", sans-serif;
  }
  .lace-pattern {
    position: absolute; inset: 0;
    background:
      radial-gradient(circle at 0% 50%, rgba(224,162,106,0.09), transparent 42%),
      radial-gradient(circle at 100% 50%, rgba(224,162,106,0.09), transparent 42%),
      radial-gradient(circle at 50% 8%, rgba(244,239,228,0.05), transparent 25%),
      radial-gradient(circle at 50% 92%, rgba(244,239,228,0.05), transparent 25%);
  }
  .frame, .panel-outline { position: absolute; left: 0; top: 0; }
  .frame-ornament {
    position: absolute; width: 44px; height: 38px; margin: -19px 0 0 -22px;
    border-radius: 50%;
    background: radial-gradient(circle, var(--copper-light) 0%, var(--copper) 45%, #2a1a10 82%);
  }
  .title {
    position: absolute; left: 0; width: 925px; text-align: center;
    font-family: "Oranienbaum", serif; font-size: 76px; line-height: 1; font-weight: 400;
  }
  .title-text { display: inline-block; }
  .title-top { top: 158px; }
  .title-top .title-text {
    background: linear-gradient(90deg, var(--copper-dark) 0%, var(--copper-light) 30%, var(--copper) 55%, #f0c49a 80%, var(--copper) 100%);
    -webkit-background-clip: text; background-clip: text; color: transparent;
  }
  .title-bottom { top: 222px; color: var(--pearl); }
  .flourish {
    position: absolute; left: 387px; top: 325px; width: 177px; height: 20px;
    background: linear-gradient(90deg, transparent, var(--copper) 30%, var(--copper-light) 50%, var(--copper) 70%, transparent);
    clip-path: ellipse(50% 30% at 50% 50%);
  }
  .tagline {
    position: absolute; left: 294px; top: 381px; width: 362px; height: 26px;
    border-top: 1px solid var(--pearl-soft); border-bottom: 1px solid var(--pearl-soft);
    text-align: center; font-weight: 600; font-size: 12.5px; letter-spacing: 5px;
    line-height: 24px; padding-left: 5px;
  }
  .event-date {
    position: absolute; left: 0; top: 422px; width: 925px; text-align: center;
    font-family: "Cinzel", serif; font-size: 48px; color: var(--pearl); letter-spacing: 0.5px;
  }
  .schedule-band {
    position: absolute; left: 0; top: 516px; width: 925px; height: 81px;
    background: linear-gradient(90deg, var(--band-edge) 0%, var(--band-mid) 30%, var(--band-center) 50%, var(--band-mid) 70%, var(--band-edge) 100%);
  }
  .band-day {
    position: absolute; left: 328px; top: 0; width: 253px; height: 81px;
    border-left: 1px solid #2c1d13; border-right: 1px solid #2c1d13;
    background: linear-gradient(90deg, #8c6a52, #a6836a 50%, #8c6a52);
    display: flex; align-items: center; justify-content: center;
    font-size: 31px; color: var(--pearl); letter-spacing: 0.5px;
  }
  .band-time {
    position: absolute; top: 15px; width: 200px; text-align: center;
    font-size: 20px; line-height: 25px; color: var(--pearl);
  }
  .band-time.social { left: 137px; }
  .band-time.dinner { left: 569px; }
  .venue {
    position: absolute; left: 0; top: 631px; width: 925px; text-align: center; font-style: normal;
  }
  .venue-name { font-size: 19.5px; letter-spacing: 2.6px; line-height: 26px; }
  .venue-address { font-size: 15.5px; line-height: 20px; }
  .dress-code {
    position: absolute; left: 65px; top: 788px; display: flex; gap: 20px;
  }
  .dress-label { font-weight: 700; font-size: 28px; line-height: 35px; }
  .dress-detail { font-size: 29px; line-height: 35px; }
  .rsvp {
    position: absolute; left: 546px; top: 757px; font-size: 23px; line-height: 30px;
  }
  .ticket { font-size: 32px; line-height: 40px; margin-top: 2px; }
  .ticket strong { font-weight: 700; color: var(--copper-light); }
</style>
</head>
<body>
  <main class="invitation">
    <div class="lace-pattern" role="img" aria-label="Faint copper lace and mandala pattern in the background"></div>

    <svg class="frame" width="925" height="925" viewBox="0 0 925 925" aria-hidden="true">
      <rect x="32" y="33" width="862" height="859" fill="none" stroke="#b87333" stroke-width="2" stroke-dasharray="60 8 10 8"/>
      <rect x="36" y="37" width="854" height="851" fill="none" stroke="#5a3a24" stroke-width="1"/>
    </svg>
    <div class="frame-ornament" style="left:462px;top:33px" role="img" aria-label="Copper scroll ornament"></div>
    <div class="frame-ornament" style="left:462px;top:892px" role="img" aria-label="Copper scroll ornament"></div>
    <div class="frame-ornament" style="left:32px;top:459px;width:38px;height:56px;margin:-28px 0 0 -19px" role="img" aria-label="Copper scroll ornament"></div>
    <div class="frame-ornament" style="left:894px;top:459px;width:38px;height:56px;margin:-28px 0 0 -19px" role="img" aria-label="Copper scroll ornament"></div>

    <svg class="panel-outline" width="925" height="925" viewBox="0 0 925 925" aria-hidden="true">
      <path d="M223 104 L425 104 Q447 104 462 78 Q477 104 499 104 L711 104 Q748 104 748 141 L748 288 Q748 305 772 319 Q748 333 748 350 L748 695 Q748 732 711 732 L499 732 Q477 732 462 761 Q447 732 425 732 L223 732 Q186 732 186 695 L186 350 Q186 333 163 319 Q186 305 186 288 L186 141 Q186 104 223 104 Z"
            fill="var(--ink)" stroke="var(--pearl-soft)" stroke-width="2"/>
    </svg>

    <h1 class="title title-top"><span class="title-text">Copper &amp; Pearl</span></h1>
    <p class="title title-bottom"><span class="title-text">Gala</span></p>
    <div class="flourish" role="img" aria-label="Copper flourish divider"></div>
    <p class="tagline">JOIN US FOR THE CELEBRATION</p>
    <p class="event-date">JUNE 3, 2023</p>

    <section class="schedule-band">
      <p class="band-time social">Social Hour<br>6:00 p.m.</p>
      <p class="band-day">SATURDAY</p>
      <p class="band-time dinner">Dinner<br>7:00 p.m.</p>
    </section>

    <address class="venue">
      <p class="venue-name">MARLOW HIGH SCHOOL GYMNASIUM</p>
      <p class="venue-address">214 Alder Street, Marlow, Kansas</p>
    </address>

    <div class="dress-code">
      <p class="dress-label">DRESS<br>CODE</p>
      <p class="dress-detail">Black &amp; White<br>Casual to Dressy</p>
    </div>

    <div class="rsvp">
      <p>RSVP<br>Monday, May 29, 2023</p>
      <p class="ticket">TICKET PRICE <strong>$30</strong></p>
    </div>
  </main>
</body>
</html>
```